Application for baby milk and water counter

We are building baby food app. Need to design main screen for tha app first so we can go forward to other secondary screens of the app

Food dashboard screen
Food dashboard screen is main page for view/edit food data

General vision
I see the app in pastel colors with some illustrations to make the app more in positive. You can influence from game Glimmer Tides. I see with smooth colors and gradients like in a game. Also need to have animations/transitions for each action. Each click should create smooth transition to new state. My idea is to build one dashboard screen for food which we can reuse it for other screens. So a lot of thinking should go into design stage to app appealing.

Food Dashboard
Current screen should show all the data about food intake of the baby. So here user should see

Milk How much food baby had in ml/oz. So there should be some kind of illustrated bottle or glass or smth that shows it is filled with that amount.

Add/Remove controls for food. Should be some kind of custom control for inputing amount to remove/add. I see it as a slider on the side of the bottle. User slides up or down and amount is added/removed.

Notification. So user should be aware how many hours/minutes left for next food intake. This is optional field, so consider it could be disabled. So no empty space should be on a screen. There should be human readable text. Something like. 1:30 minutes left for next intake. Maybe could be some custom made icons to illustrate that it is next food intake.

Burped: User should have ability to how much baby burped. This amount is integer value. So it could be “Baby burped 2 times today”. So again here I see some custom made/icon to illustrate how many times baby burped and amount next to it. I see changing the value just by tapping, but I don’t know how to edit if user tapped accidentally more than it should be. So TBD here.

Date and time: Dashboard should show for which date it is viewing/editing data. Should be able to change it, so user can add/edit data for yesterday. Don’t want to see here calendar on a screen so need to come up with nice design decision.

Water: User should have ability to view/edit water intake of the baby, but water is secondary information so it should be smaller than milk, or come up with some other idea how to show the water. I see to have same controls for water like for milk. Water intake is optional it can be disabled by the user.

Target Market(s)

For just became mothers

Font styles to use
Sans Serif

Colors
0094D4
00A9DD
6FCCEA
C7EBF8
E9F6FB
FFC000
F8CF3A
FAE287
FDF2CF
FEFAEE
E54698
E96AAD
F1A4CE
F9D9EA
FCEFF6

Requirements
Must have
• Ilustrations or playfull icons for show information

```html
<!DOCTYPE html>
<html lang="en">
<head>
<meta charset="utf-8">
<title>Food Dashboard</title>
<link rel="stylesheet" href="https://fonts.googleapis.com/css2?family=Comic+Neue:wght@400;700&display=swap">
<style>
:root{
  --blue-dark:#0094D4;
  --blue:#00A9DD;
  --blue-mid:#6FCCEA;
  --blue-light:#C7EBF8;
  --blue-pale:#E9F6FB;
  --yellow:#FFC000;
  --yellow-soft:#F8CF3A;
  --cream:#FEFAEE;
  --cream-mid:#FDF2CF;
  --pink:#E54698;
  --pink-mid:#E96AAD;
  --pink-light:#F1A4CE;
  --pink-pale:#F9D9EA;
  --white:#ffffff;
  --ink:#111111;
}
*{box-sizing:border-box;margin:0;padding:0}
html,body{width:667px;height:1200px;overflow:hidden}
body{font-family:"Comic Neue",sans-serif;color:var(--ink)}
.dashboard{position:relative;width:667px;height:1200px;overflow:hidden;
  background:linear-gradient(180deg,#F2B1D6 0%,#D6B4E0 30%,#B5C0E8 60%,#86D3EF 100%)}
.date-picker{position:absolute;top:43px;left:112px;display:flex;gap:11px}
.date-select{width:142px;height:46px;border-radius:23px;background:var(--white);display:flex;
  align-items:center;justify-content:space-between;padding:0 22px 0 28px;font-size:20px}
.date-select svg{width:12px;height:16px}
.current-date-title{position:absolute;top:108px;left:0;width:667px;text-align:center;font-size:29px;font-weight:700;letter-spacing:.5px}
.current-date{position:absolute;top:153px;left:228px;width:208px;height:47px;border-radius:24px;background:var(--white);
  display:flex;align-items:center;justify-content:center;font-size:22px;font-weight:700;letter-spacing:1.5px}
.bottle-title{position:absolute;color:var(--pink);font-weight:700;letter-spacing:.5px}
.bottle-title.milk{top:258px;left:134px;font-size:31px}
.bottle-title.water{top:388px;left:357px;font-size:31px}
.bottle{position:absolute;border:2px solid var(--ink);
  background:linear-gradient(180deg,var(--cream-mid) 0%,var(--cream) 35%,var(--cream) 100%)}
.bottle.milk{left:99px;top:320px;width:178px;height:607px;border-radius:70px 70px 48px 48px}
.bottle.water{left:372px;top:460px;width:147px;height:467px;border-radius:60px 60px 40px 40px}
.scale{position:absolute;
  background:repeating-linear-gradient(180deg,var(--ink) 0 2px,transparent 2px 10.7px)}
.scale.milk{left:253px;top:551px;width:22px;height:324px}
.scale.water{left:491px;top:637px;width:16px;height:252px}
.volume-mark{position:absolute;font-size:19px;display:flex;align-items:center}
.volume-mark::before{content:"";width:20px;height:2px;background:var(--ink);margin-right:4px}
.volume-mark.milk{left:277px;top:497px}
.volume-mark.water{left:510px;top:593px}
.water-toggle{position:absolute;top:494px;left:565px;display:flex;align-items:center;gap:5px;font-size:16px}
.toggle{width:22px;height:12px;border-radius:6px;background:var(--ink);position:relative}
.toggle::after{content:"";position:absolute;left:2px;top:2px;width:8px;height:8px;border-radius:50%;background:var(--white)}
.level-label{position:absolute;top:526px;color:var(--blue-dark);font-size:24px}
.level-label.milk{left:19px}
.level-label.water{left:579px}
.level-slider{position:absolute;top:574px;width:8px;height:353px;border-radius:4px;background:var(--white)}
.level-slider.milk{left:47px}
.level-slider.water{left:608px}
.level-fill{position:absolute;left:0;bottom:0;width:100%;height:121px;border-radius:0 0 4px 4px;background:var(--yellow)}
.level-knob{position:absolute;left:-9px;top:219px;width:26px;height:26px;border-radius:50%;background:var(--yellow);border:4px solid var(--white)}
.burp-label{position:absolute;top:976px;left:177px;color:var(--blue-dark);font-size:24.5px}
.burp-stepper{position:absolute;top:971px;left:350px;width:138px;height:45px;border-radius:23px;background:var(--white);
  display:flex;align-items:center;justify-content:space-between;padding:0 16px;font-size:19px}
.burp-stepper svg{width:18px;height:18px}
.intake-reminder{position:absolute;top:1067px;left:153px;width:375px;height:48px;border-radius:24px;background:var(--blue);
  color:var(--white);font-weight:700;font-size:20.5px;letter-spacing:.8px;display:flex;align-items:center;padding-left:74px}
.reminder-icon{position:absolute;top:1058px;left:139px;width:72px;height:72px;border-radius:50%;background:var(--pink);
  border:5px solid var(--white);display:flex;align-items:center;justify-content:center}
.reminder-icon svg{width:30px;height:30px}
</style>
</head>
<body>
<main class="dashboard" role="img" aria-label="Pastel gradient background with faint baby bottle doodles">
  <div class="date-picker">
    <div class="date-select">Date<svg viewBox="0 0 12 16"><path d="M1 6 6 1l5 5zM1 10l5 5 5-5z" fill="#111"/></svg></div>
    <div class="date-select">Month<svg viewBox="0 0 12 16"><path d="M1 6 6 1l5 5zM1 10l5 5 5-5z" fill="#111"/></svg></div>
    <div class="date-select">Year<svg viewBox="0 0 12 16"><path d="M1 6 6 1l5 5zM1 10l5 5 5-5z" fill="#111"/></svg></div>
  </div>
  <h1 class="current-date-title">Current Date</h1>
  <div class="current-date">May, 31, 2023</div>

  <h2 class="bottle-title milk">Milk Bottle</h2>
  <div class="bottle milk" role="img" aria-label="Illustrated milk bottle with teat and collar, filled with milk"></div>
  <div class="scale milk"></div>
  <span class="volume-mark milk">200ml</span>

  <h2 class="bottle-title water">Water Bottle</h2>
  <div class="bottle water" role="img" aria-label="Illustrated smaller water bottle with teat and collar"></div>
  <div class="scale water"></div>
  <span class="volume-mark water">100ml</span>

  <div class="water-toggle">On <span class="toggle"></span> Off</div>

  <span class="level-label milk">Level</span>
  <div class="level-slider milk"><div class="level-fill"></div><div class="level-knob"></div></div>
  <span class="level-label water">Level</span>
  <div class="level-slider water"><div class="level-fill"></div><div class="level-knob"></div></div>

  <span class="burp-label">Times Burped</span>
  <div class="burp-stepper">
    <svg viewBox="0 0 18 18"><rect x="1" y="7.5" width="16" height="3" fill="#111"/></svg>
    <span>2</span>
    <svg viewBox="0 0 18 18"><rect x="1" y="7.5" width="16" height="3" fill="#111"/><rect x="7.5" y="1" width="3" height="16" fill="#111"/></svg>
  </div>

  <div class="intake-reminder">2 hours left for next intake</div>
  <div class="reminder-icon">
    <svg viewBox="0 0 24 24"><path d="M12 2a2 2 0 0 1 2 2v.3A6.5 6.5 0 0 1 18.5 10.5V15l2 3H3.5l2-3v-4.5A6.5 6.5 0 0 1 10 4.3V4a2 2 0 0 1 2-2zm-2.5 17.5h5a2.5 2.5 0 0 1-5 0z" fill="#fff"/></svg>
  </div>
</main>
</body>
</html>
```